Harborview Estates Business Card for Apartment Buildings

Create business cards for resident managers who run apartment buildings. The audience is the public who are searching for apartment rentals, and current residents who live at the apartment building. Key design element will be incorporating the company logo, however, the logo cannot dominate. The building name and manager name are more important than the logo. Current business card design leaves little room for copy, so we may need to reduce the size on the current card to allow for more space for copy.

Target Market(s)

Adults 18-65 years of age, who are looking for an apartment rental, plus current residents who live at our apartment buildings.

Industry/Entity Type

Property Management

Contact Information for Business Card

A major design element will be use of the company logo. Important property and manager contact information must be part of the design. The size of the logo will need to be reduced to make room for building and manager contact copy.

Font styles to use
Sans Serif

Colors
3176b5
000000
959595
ffffff

Requirements
Must have
• 1) Incorporate the company logo.
• 2) Use the company colors (dark blue, black/grey, over white).
• 3) FEATURE THE BUILDING NAME
• 4) FEATURE THE MANAGER NAME
• 5) The company name is less important than BUILDING and MANAGER
• 6) Manager contact information
• **SEE ATTACHED CREATIVE BRIEF**
Nice to have
• 1) Back of card logo watermark
• 2) Ability to write notes on back of carfd
Should not have
• Avoid letting the company logo dominate the card, the building name and manager are more important than the company logo.

```html
<!DOCTYPE html>
<html lang="en">
<head>
<meta charset="utf-8">
<title>Harborview Estates Business Card</title>
<link href="https://fonts.googleapis.com/css2?family=Roboto:wght@400;500;700&family=Roboto+Condensed:wght@700&display=swap" rel="stylesheet">
<style>
  :root {
    --brand-blue: #1a6fae;
    --brand-blue-back: #1b6cab;
    --ink-grey: #3f3f3f;
    --mid-grey: #959595;
    --band-grey: #4a4a4a;
    --paper: #f4f4f4;
    --stage: #2a2a2a;
    --white: #ffffff;
  }
  * { margin: 0; padding: 0; box-sizing: border-box; }
  html, body { width: 1200px; height: 960px; overflow: hidden; background: var(--stage); }
  .canvas { position: relative; width: 1200px; height: 960px; font-family: "Roboto", Arial, sans-serif; }

  .card { position: absolute; left: 320px; width: 600px; height: 342px; overflow: hidden; }

  .card-back { top: 104px; background: var(--brand-blue-back); }
  .card-back .watermark-name {
    position: absolute; left: 0; right: 0; top: 148px; text-align: center;
    font-weight: 700; font-size: 40px; letter-spacing: 2px;
    color: rgba(255,255,255,0.12);
  }

  .card-front { top: 493px; background: var(--paper); }

  .company-name {
    position: absolute; left: 66px; top: 156px; width: 230px;
    font-weight: 700; font-size: 19px; line-height: 1.1; color: var(--brand-blue);
  }
  .company-name .mark-dot {
    display: inline-block; width: 14px; height: 14px; border-radius: 50%;
    background: var(--brand-blue); margin-right: 8px; vertical-align: -1px;
  }

  .divider { position: absolute; left: 307px; top: 68px; width: 1px; height: 200px; background: #c9c9c9; }

  .contact-block { position: absolute; left: 332px; top: 70px; color: var(--ink-grey); }
  .manager-name { font-family: "Roboto Condensed", Arial, sans-serif; font-weight: 700; font-size: 23px; color: var(--brand-blue); line-height: 28px; }
  .manager-title { font-weight: 500; font-size: 15px; line-height: 20px; }
  .building-name { font-weight: 700; font-size: 15px; color: var(--brand-blue); margin-top: 10px; line-height: 20px; }
  .address { font-size: 14px; line-height: 18px; }
  .contact-list { list-style: none; margin-top: 9px; }
  .contact-list li { display: flex; align-items: center; font-size: 14px; line-height: 19px; }
  .contact-list svg { width: 13px; height: 13px; margin-right: 8px; fill: var(--brand-blue); flex: none; }

  .base-band { position: absolute; left: 0; right: 0; bottom: 0; height: 7px; background: var(--band-grey); }
  .web-tab {
    position: absolute; left: 143px; bottom: 0; width: 315px; height: 29px;
    background: var(--brand-blue);
    clip-path: polygon(18px 0, 297px 0, 100% 100%, 0 100%);
    color: var(--white); font-size: 14px; letter-spacing: 3.2px;
    display: flex; align-items: center; justify-content: center; padding-top: 2px;
  }
</style>
</head>
<body>
<div class="canvas">
  <section class="card card-back">
    <div class="watermark-name">HARBORVIEW ESTATES</div>
  </section>

  <section class="card card-front">
    <div class="company-name"><span class="mark-dot"></span>HARBORVIEW ESTATES LLC</div>
    <div class="divider"></div>
    <div class="contact-block">
      <div class="manager-name">Marisol Quintero</div>
      <div class="manager-title">Resident Manager</div>
      <div class="building-name">Cedar Crest Apartments</div>
      <div class="address">2485 Larkspur Avenue<br>Coral Bay, CA 92017</div>
      <ul class="contact-list">
        <li><svg viewBox="0 0 16 16"><path d="M3.6 1l2.6 3-1.5 1.8c.9 2 2.5 3.6 4.5 4.5L11 8.8l3 2.6-1.4 3C7 14.6 1.4 9 1.6 3.4z"/></svg>555-014-2231</li>
        <li><svg viewBox="0 0 16 16"><path d="M4 0h8v16H4zM5.5 1.5v11h5v-11zM7.3 13.6h1.4v1.2H7.3z"/></svg>555-018-4470</li>
        <li><svg viewBox="0 0 16 16"><path d="M4 1h8v4H4zM1 6h14v7h-2v-3H3v3H1zM4 11h8v4H4z"/></svg>555-016-9025</li>
        <li><svg viewBox="0 0 16 16"><path d="M1 3h14v1.2L8 9 1 4.2zM1 5.8l7 4.8 7-4.8V13H1z"/></svg>marisol@harborviewest.com</li>
      </ul>
    </div>
    <div class="base-band"></div>
    <div class="web-tab">www.harborviewest.com</div>
  </section>
</div>
</body>
</html>
```